Nivel Crest - Powerpoint Templates

We are a consultancy to help builders to optimize their planning in order to save building costs. For that reason we need templates for teasers and presentations where we offer our services, show our team and their capacities and present workflows, organization charts, price lists etc.

```html
<!DOCTYPE html>
<html lang="en">
<head>
<meta charset="utf-8">
<title>Nivel Crest – Presentation Template</title>
<link rel="stylesheet" href="https://fonts.googleapis.com/css2?family=Orbitron:wght@700;800;900&family=Roboto:wght@400;500&display=swap">
<style>
:root{
  --gold:#c98f35;
  --gold-light:#f0cb6c;
  --gold-pale:#ead1a4;
  --brown:#98570f;
  --yellow:#ecc444;
  --slate:#55565b;
  --slate-dark:#2e2f33;
  --ink:#111111;
  --text:#5b5b5b;
  --track:#f1f1f1;
}
*{margin:0;padding:0;box-sizing:border-box}
html,body{width:1200px;height:3868px;overflow:hidden;background:#fff}
body{position:relative;font-family:"Roboto",Arial,sans-serif;color:var(--text)}
.slide{position:absolute;left:108px;width:982px;height:553px;background:#fff;overflow:hidden;box-shadow:0 0 6px rgba(0,0,0,.08)}
.abs{position:absolute}
.heading{font-family:"Orbitron",Arial,sans-serif;font-weight:800;color:var(--ink);letter-spacing:1px}
.body-copy{font-size:10px;line-height:20.5px;color:var(--text)}
.side-bar{position:absolute;left:0;top:0;width:51px;height:553px;border-radius:26px;background:linear-gradient(180deg,var(--gold-light),var(--gold))}
.brand{display:flex;align-items:center;gap:10px}
.brand-mark{width:26px;height:26px;background:var(--gold)}
.brand-name{font-family:"Orbitron",Arial,sans-serif;font-weight:800;color:var(--gold);font-size:22px;letter-spacing:1px}

/* cover */
.cover-title{left:82px;top:236px;font-size:35px;line-height:50px}

/* about */
.about-title{left:102px;top:74px;font-size:28px}
.about-text{left:102px;top:143px;width:390px}
.about-text p+p{margin-top:20px}
.about-photo{left:544px;top:93px;width:356px;height:367px;border-radius:0 48px 0 48px;background:linear-gradient(160deg,#8fa3ad 0%,#b9a48a 45%,#e39a3c 75%,#3a2a1e 100%)}

/* workflow */
.center-block{left:0;width:982px;text-align:center}
.wf-title{top:46px;font-size:27px}
.wf-intro{top:96px;font-size:10px;line-height:21px}
.wf-outro{top:440px;font-size:10px;line-height:21px}
.tl-label{font-size:8px;color:var(--text);transform:translateX(-50%);white-space:nowrap}

/* org chart */
.org-title{left:80px;top:82px;font-size:26px}
.bar-track{left:80px;width:398px;height:30px;border-radius:15px;background:#fff;box-shadow:0 1px 4px rgba(0,0,0,.18)}
.bar-fill{position:absolute;left:0;top:0;height:30px;border-radius:15px}
.bar-fill.brown{background:var(--brown)}
.bar-fill.yellow{background:var(--yellow)}
.bar-value{position:absolute;right:18px;top:8px;font-size:9px;font-weight:500;color:var(--brown)}
.org-text{left:538px;top:108px;width:368px}
.org-list{left:564px;top:310px;width:350px;list-style:none}
.org-list li{position:relative;padding-left:16px;margin-bottom:8px}
.org-list li::before{content:"";position:absolute;left:0;top:6px;width:9px;height:9px;border-radius:50%;background:var(--gold)}

/* team */
.team-title{top:78px;font-size:27px}
.team-intro{top:128px;font-size:10px;line-height:21px}
.team-card{top:230px;width:177px;height:228px;background:#fff;box-shadow:0 0 8px rgba(0,0,0,.08);text-align:center}
.avatar{margin:24px auto 0;width:72px;height:72px;border-radius:50%;border:4px solid var(--gold);background:linear-gradient(180deg,#8b8f96,#4b4e55)}
.member-name{margin-top:12px;font-family:"Orbitron",Arial,sans-serif;font-weight:800;font-size:11px;color:var(--ink)}
.member-bio{margin:8px auto 0;width:140px;font-size:8px;line-height:15px}
.social-dot{margin:8px auto 0;width:13px;height:13px;border-radius:50%;background:var(--gold)}

/* contact */
.contact-col{top:254px;width:240px;text-align:center;font-size:10px;line-height:21px}
.contact-icon{margin:0 auto 14px;width:42px;height:42px;border-radius:50%;background:var(--slate);display:flex;align-items:center;justify-content:center}
.thanks{top:398px;font-size:44px}
</style>
</head>
<body>

<!-- Cover -->
<section class="slide" style="top:102px">
  <svg class="abs" style="left:0;top:0" width="982" height="553" viewBox="0 0 982 553" aria-hidden="true">
    <defs>
      <linearGradient id="slateGrad" x1="0" y1="0" x2="1" y2="1"><stop offset="0" stop-color="#6b6c71"/><stop offset="1" stop-color="#2e2f33"/></linearGradient>
      <linearGradient id="cityGrad" x1="0" y1="0" x2="1" y2="1"><stop offset="0" stop-color="#6f7e8c"/><stop offset=".45" stop-color="#8fb7d8"/><stop offset="1" stop-color="#5a4a3c"/></linearGradient>
    </defs>
    <polygon points="300,0 330,0 470,168 440,168" fill="var(--gold-pale)"/>
    <polygon points="345,0 390,0 590,250 550,250" fill="var(--gold)"/>
    <polygon points="660,400 700,400 820,553 780,553" fill="var(--gold-pale)"/>
    <polygon points="0,352 0,553 235,553" fill="url(#slateGrad)"/>
    <polygon points="90,448 125,448 245,553 210,553" fill="var(--gold)"/>
  </svg>
  <div class="abs" role="img" aria-label="Photo of high-rise buildings against a bright sky" style="left:0;top:0;width:982px;height:553px;background:linear-gradient(135deg,#6f7e8c,#8fb7d8 45%,#5a4a3c);clip-path:polygon(400px 0,982px 0,982px 553px,850px 553px,560px 200px)"></div>
  <div class="abs brand" style="left:82px;top:146px"><span class="brand-mark"></span><span class="brand-name">NIVEL CREST</span></div>
  <h1 class="abs heading cover-title">WELCOME TO<br>NIVEL CREST</h1>
</section>

<!-- About -->
<section class="slide" style="top:724px">
  <div class="side-bar"></div>
  <h2 class="abs heading about-title">ABOUT US</h2>
  <div class="abs body-copy about-text">
    <p>On the other hand, we denounce with righteous indignation and dislike men who are so beguiled and demoralized by the charms of pleasure of the moment, so blinded by desire, that they cannot foresee the pain and trouble that are bound to ensue; and equal blame belongs to those who fail in their duty through weakness of will, which is the same as saying through shrinking from toil and pain. These cases are perfectly simple and easy to distinguish. In a free hour, when our power of choice is untrammelled and when nothing prevents our being able to do what we like best, every pleasure is to be welcomed and every pain avoided. But in certain circumstances and owing to the claims of duty or the obligations of business it will frequently occur that pleasures have to be repudiated and annoyances accepted.</p>
    <p>On the other hand, we denounce with righteous indignation and dislike men who are so beguiled and demoralized by the charms of pleasure of the moment, so blinded by desire, that they cannot foresee the pain and trouble that are bound to ensue; and equal blame belongs to those who fail in their duty through</p>
  </div>
  <div class="abs about-photo" role="img" aria-label="Photo of construction workers silhouetted on scaffolding at sunset"></div>
</section>

<!-- Workflow -->
<section class="slide" style="top:1345px">
  <div class="side-bar"></div>
  <h2 class="abs heading center-block wf-title">OUR CAPACITIES &amp; PRESENT WORKFLOWS</h2>
  <p class="abs center-block wf-intro">I must explain to you how all this mistaken idea of denouncing pleasure and praising pain was born and I will give you a complete account of<br>the system, and expound the actual teachings of the great explorer of the truth, the master-builder of human happiness. No one</p>
  <svg class="abs" style="left:0;top:0" width="982" height="553" viewBox="0 0 982 553" aria-hidden="true">
    <g stroke="var(--gold-light)" stroke-width="1.5">
      <line x1="112" y1="285" x2="868" y2="285"/>
      <line x1="112" y1="285" x2="112" y2="365"/>
      <line x1="196" y1="207" x2="196" y2="285"/>
      <line x1="280" y1="285" x2="280" y2="365"/>
      <line x1="364" y1="207" x2="364" y2="285"/>
      <line x1="448" y1="285" x2="448" y2="365"/>
      <line x1="532" y1="207" x2="532" y2="285"/>
      <line x1="616" y1="285" x2="616" y2="365"/>
      <line x1="700" y1="207" x2="700" y2="285"/>
      <line x1="784" y1="285" x2="784" y2="365"/>
      <line x1="868" y1="207" x2="868" y2="285"/>
    </g>
    <g fill="var(--gold)" stroke="var(--gold-light)" stroke-width="3">
      <circle cx="112" cy="285" r="5"/><circle cx="196" cy="285" r="5"/><circle cx="280" cy="285" r="5"/><circle cx="364" cy="285" r="5"/><circle cx="448" cy="285" r="5"/>
      <circle cx="532" cy="285" r="5"/><circle cx="616" cy="285" r="5"/><circle cx="700" cy="285" r="5"/><circle cx="784" cy="285" r="5"/><circle cx="868" cy="285" r="5"/>
    </g>
  </svg>
  <span class="abs tl-label" style="left:112px;top:264px;transform:none;margin-left:-10px">1996</span>
  <span class="abs tl-label" style="left:196px;top:183px">Lorem Lipsum</span>
  <span class="abs tl-label" style="left:364px;top:183px">Lorem Lipsum</span>
  <span class="abs tl-label" style="left:532px;top:183px">Lorem Lipsum</span>
  <span class="abs tl-label" style="left:700px;top:183px">Lorem Lipsum</span>
  <span class="abs tl-label" style="left:868px;top:183px">Lorem Lipsum</span>
  <span class="abs tl-label" style="left:112px;top:379px">Lorem Lipsum</span>
  <span class="abs tl-label" style="left:280px;top:379px">Lorem Lipsum</span>
  <span class="abs tl-label" style="left:448px;top:379px">Lorem Lipsum</span>
  <span class="abs tl-label" style="left:616px;top:379px">Lorem Lipsum</span>
  <span class="abs tl-label" style="left:784px;top:379px">Lorem Lipsum</span>
  <p class="abs center-block wf-outro">I must explain to you how all this mistaken idea of denouncing pleasure and praising pain was born and I will give you a complete account of<br>the system, and expound the actual teachings of the great explorer of the truth, the master-builder of human happiness. No one<br>rejects, dislikes, or avoids pleasure itself, because it is pleasure, but because those who do not know</p>
</section>

<!-- Organization charts -->
<section class="slide" style="top:1966px">
  <div class="side-bar"></div>
  <h2 class="abs heading org-title">ORGANIZATION CHARTS</h2>
  <div class="abs bar-track" style="top:149px"><div class="bar-fill brown" style="width:222px"></div><span class="bar-value">60%</span></div>
  <div class="abs bar-track" style="top:196px"><div class="bar-fill yellow" style="width:279px"></div><span class="bar-value">80%</span></div>
  <div class="abs bar-track" style="top:244px"><div class="bar-fill brown" style="width:166px"></div><span class="bar-value">40%</span></div>
  <div class="abs bar-track" style="top:291px"><div class="bar-fill yellow" style="width:131px"></div><span class="bar-value">30%</span></div>
  <div class="abs bar-track" style="top:338px"><div class="bar-fill brown" style="width:258px"></div><span class="bar-value">70%</span></div>
  <div class="abs bar-track" style="top:386px"><div class="bar-fill yellow" style="width:217px"></div><span class="bar-value">60%</span></div>
  <div class="abs bar-track" style="top:433px"><div class="bar-fill brown" style="width:315px"></div><span class="bar-value">90%</span></div>
  <div class="abs body-copy org-text">
    <p>On the other hand, we denounce with righteous indignation and dislike men who are so beguiled and demoralized by the charms of pleasure of the moment, so blinded by desire, that they cannot foresee the pain and trouble that are bound to ensue; and equal blame belongs to those who fail in their duty through weakness of will, which is the same as saying through shrinking from toil and pain. These cases are perfectly simple and easy to distinguish.</p>
    <p style="margin-top:20px">In a free hour, when our power of choice is untrammelled and when nothing prevents our being able to do what we like</p>
  </div>
  <ul class="abs body-copy org-list">
    <li>In a free hour, when our power of choice is untrammelled and when nothing prevents our being able to do what</li>
    <li>In a free hour, when our power of choice is untrammelled and when nothing prevents our being able to do what</li>
    <li>In a free hour, when our power of choice is untrammelled and when nothing prevents our being able to do what</li>
  </ul>
</section>

<!-- Team -->
<section class="slide" style="top:2587px">
  <div class="side-bar"></div>
  <h2 class="abs heading center-block team-title">OUR TEAM</h2>
  <p class="abs center-block team-intro">I must explain to you how all this mistaken idea of denouncing pleasure and praising pain was born and I will give you a complete account of the<br>system, and expound the actual teachings of the great explorer of the truth, the master-builder of human happiness. No one rejects, dislikes, or<br>avoids pleasure itself, because it is pleasure, but because those who do not know how to pursue</p>
  <article class="abs team-card" style="left:102px">
    <div class="avatar" role="img" aria-label="Portrait photo of John Smith"></div>
    <h3 class="member-name">JOHN SMITH</h3>
    <p class="member-bio">I must explain to you how all this mistaken idea of denouncing pleasure and praising pain</p>
    <div class="social-dot"></div>
  </article>
  <article class="abs team-card" style="left:303px">
    <div class="avatar" role="img" aria-label="Portrait photo of Alexa Mathew"></div>
    <h3 class="member-name">ALEXA MATHEW</h3>
    <p class="member-bio">I must explain to you how all this mistaken idea of denouncing pleasure and praising pain</p>
    <div class="social-dot"></div>
  </article>
  <article class="abs team-card" style="left:504px">
    <div class="avatar" role="img" aria-label="Portrait photo of John Hendry"></div>
    <h3 class="member-name">JOHN HENDRY</h3>
    <p class="member-bio">I must explain to you how all this mistaken idea of denouncing pleasure and praising pain</p>
    <div class="social-dot"></div>
  </article>
  <article class="abs team-card" style="left:705px">
    <div class="avatar" role="img" aria-label="Portrait photo of Mathew Smith"></div>
    <h3 class="member-name">MATHEW SMITH</h3>
    <p class="member-bio">I must explain to you how all this mistaken idea of denouncing pleasure and praising pain</p>
    <div class="social-dot"></div>
  </article>
</section>

<!-- Contact -->
<section class="slide" style="top:3208px">
  <svg class="abs" style="left:0;top:0" width="982" height="553" viewBox="0 0 982 553" aria-hidden="true">
    <polygon points="660,0 690,0 790,110 760,110" fill="var(--gold-pale)"/>
    <polygon points="700,0 735,0 855,140 820,140" fill="var(--gold)"/>
    <polygon points="900,230 930,230 982,292 982,330" fill="var(--gold-pale)"/>
    <polygon points="0,352 0,553 235,553" fill="url(#slateGrad)"/>
    <polygon points="90,448 125,448 245,553 210,553" fill="var(--gold)"/>
  </svg>
  <div class="abs" role="img" aria-label="Photo of a glass skyscraper" style="left:0;top:0;width:982px;height:553px;background:linear-gradient(135deg,#8fb7d8,#5c6670);clip-path:polygon(760px 0,982px 0,982px 260px)"></div>
  <div class="abs brand" style="left:0;width:982px;top:140px;justify-content:center;gap:14px">
    <span class="brand-mark" style="width:40px;height:40px"></span><span class="brand-name" style="font-size:34px">NIVEL CREST</span>
  </div>
  <div class="abs contact-col" style="left:129px">
    <div class="contact-icon"><svg width="20" height="20" viewBox="0 0 24 24" fill="#fff"><path d="M12 2a7 7 0 0 0-7 7c0 5 7 13 7 13s7-8 7-13a7 7 0 0 0-7-7zm0 9.5A2.5 2.5 0 1 1 12 6.5a2.5 2.5 0 0 1 0 5z"/></svg></div>
    Lorem ipsum dolor sit amet, consectetur<br>adipiscing elit, sed do eiusmod
  </div>
  <div class="abs contact-col" style="left:370px">
    <div class="contact-icon"><svg width="20" height="20" viewBox="0 0 24 24" fill="#fff"><path d="M6.6 10.8a15 15 0 0 0 6.6 6.6l2.2-2.2a1 1 0 0 1 1-.25 11.4 11.4 0 0 0 3.6.57 1 1 0 0 1 1 1V20a1 1 0 0 1-1 1A17 17 0 0 1 3 4a1 1 0 0 1 1-1h3.5a1 1 0 0 1 1 1c0 1.25.2 2.45.57 3.57a1 1 0 0 1-.25 1z"/></svg></div>
    Contact Number<br>+1 888 8888 8888 (or) +1 999 9999 9999
  </div>
  <div class="abs contact-col" style="left:612px">
    <div class="contact-icon"><svg width="20" height="20" viewBox="0 0 24 24" fill="none" stroke="#fff" stroke-width="2"><rect x="3" y="5" width="18" height="14" rx="1"/><path d="M3 6l9 7 9-7"/></svg></div>
    Email Address<br>info@nivelcrest.example
  </div>
  <h2 class="abs heading center-block thanks">THANK YOU</h2>
</section>

</body>
</html>
```